International Clinical Software Company needs a new business card design

We are looking for a new business card design for our company that has recently expanded into the UK market, making us a multinational company.
After having rebranded our website and produced a new style guide, we are looking for a business card that is creative and attention grabbing, while being consistent with the style and colour scheme used on the new website, www.plumvora.example
We produce care management technology for the aged care market, but the main aspect we aim to communicate is the human element of our software, and the way it assists in providing better care for aged people, and stronger relationships between aged people and the staff that care for them.
Our current business card is a dark green with gold text, which makes the text quite difficult to read, not very aesthetically appealing and the colour scheme looks quite dated.
We would like something fresh and modern, that can still be colourful but doesn't use large blocks of dark colour, and uses the colours within our logo.
Something tying in with the leaves that are used in our logo could work quite nicely, along with the Autumn/Fall colours of soft greens, yellows and reds (also in our existing logo). However also happy to look at fresh, completely out of the box ideas we may not have yet considered.
Target Market(s)
The people that receive this business card work in the aged card or health industry and are either corporate/management level staff or clinical (Registered Nurses, care workers etc.)
Industry/Entity Type
Health Product
Contact Information for Business Card
Company Name - BrindlewayCare
Company locations: United Kingdom, Australia, New Zealand
Staff Details:
Staff name: Derek Mallow
Staff job title: Executive Chairman
Staff email: d.mallow@plumvora.example
Office phone number: 01742 918576
Font styles to use
Other font styles liked:
- Calibri
Requirements
Must have
- Must include the BrindlewayCare brand name in it's current font
- Must include logo (3 leaves in gold circle)
- Must include Business Card Details
Nice to have
- Elements of gold
- White space
- Something autumn themed but not too cliched
Should not have
- No blue - used by a major competitor and we would like to differentiate from them
- Large blocks of dark green colour (the green that appears in our leaves on the logo on our current business card is the background colour and it is far too dark)

```html
<!DOCTYPE html>
<html lang="en">
<head>
<meta charset="utf-8">
<title>BrindlewayCare – Business Card</title>
<link rel="stylesheet" href="https://fonts.googleapis.com/css2?family=Arimo:wght@400;700&display=swap">
<style>
  :root {
    --page-bg: #ecebe7;
    --card-bg: #ffffff;
    --gold: #b9a47c;
    --gold-dark: #a08b63;
    --crimson: #c3184e;
    --text-grey: #6b6b6b;
    --divider: #d8cdb6;
    --leaf-amber: rgba(232, 170, 92, 0.75);
    --leaf-honey: rgba(242, 206, 140, 0.55);
    --leaf-rust: rgba(214, 128, 84, 0.45);
  }
  * { box-sizing: border-box; margin: 0; padding: 0; }
  html, body {
    width: 1200px;
    height: 950px;
    overflow: hidden;
    background: var(--page-bg);
    font-family: "Arimo", Arial, sans-serif;
  }
  .business-card {
    position: absolute;
    left: 75px;
    top: 175px;
    width: 1050px;
    height: 600px;
    background: var(--card-bg);
    overflow: hidden;
    box-shadow: 0 10px 30px rgba(0,0,0,0.12);
  }
  .autumn-foliage {
    position: absolute;
    right: 0;
    top: 0;
    width: 680px;
    height: 470px;
    background:
      radial-gradient(ellipse 220px 160px at 78% 16%, var(--leaf-rust), transparent 70%),
      radial-gradient(ellipse 300px 200px at 70% 30%, var(--leaf-amber), transparent 72%),
      radial-gradient(ellipse 420px 300px at 62% 34%, var(--leaf-honey), transparent 75%);
  }
  .brand {
    position: absolute;
    left: 70px;
    top: 130px;
  }
  .brand-mark {
    width: 120px;
    height: 120px;
    border-radius: 50%;
    background: var(--gold);
    margin-bottom: 24px;
  }
  .brand-name {
    font-size: 62px;
    font-weight: 400;
    color: var(--gold);
    letter-spacing: 1px;
    line-height: 1;
  }
  .contact {
    position: absolute;
    left: 70px;
    top: 350px;
  }
  .person-name {
    font-size: 30px;
    font-weight: 700;
    color: var(--gold);
    line-height: 1.2;
  }
  .person-title {
    font-size: 25px;
    color: var(--crimson);
    line-height: 1.3;
    margin-bottom: 10px;
  }
  .contact-list { list-style: none; }
  .contact-item {
    display: flex;
    align-items: center;
    gap: 12px;
    font-size: 24px;
    color: var(--text-grey);
    line-height: 36px;
  }
  .contact-icon { width: 22px; height: 22px; flex: none; }
  .divider {
    position: absolute;
    left: 500px;
    top: 360px;
    width: 2px;
    height: 150px;
    background: var(--divider);
  }
  .locations {
    position: absolute;
    left: 530px;
    top: 372px;
    font-size: 24px;
    color: var(--text-grey);
    line-height: 36px;
  }
</style>
</head>
<body>
  <article class="business-card">
    <div class="autumn-foliage" role="img" aria-label="Soft photograph of autumn leaves on branches fading into white"></div>

    <header class="brand">
      <div class="brand-mark"></div>
      <div class="brand-name">BrindlewayCare</div>
    </header>

    <section class="contact">
      <div class="person-name">Derek Mallow</div>
      <div class="person-title">Executive Chairman</div>
      <ul class="contact-list">
        <li class="contact-item">
          <svg class="contact-icon" viewBox="0 0 24 24" aria-hidden="true">
            <path fill="var(--gold-dark)" d="M6.6 10.8a15 15 0 0 0 6.6 6.6l2.2-2.2a1 1 0 0 1 1-.25 11.4 11.4 0 0 0 3.6.57 1 1 0 0 1 1 1V20a1 1 0 0 1-1 1A17 17 0 0 1 3 4a1 1 0 0 1 1-1h3.5a1 1 0 0 1 1 1c0 1.25.2 2.45.57 3.6a1 1 0 0 1-.25 1z"/>
          </svg>
          01742 918576
        </li>
        <li class="contact-item">
          <svg class="contact-icon" viewBox="0 0 24 24" aria-hidden="true">
            <rect x="2" y="5" width="20" height="14" rx="1.5" fill="var(--gold-dark)"/>
            <path d="M3 6l9 7 9-7" fill="none" stroke="#fff" stroke-width="1.6"/>
          </svg>
          d.mallow@plumvora.example
        </li>
        <li class="contact-item">
          <svg class="contact-icon" viewBox="0 0 24 24" aria-hidden="true">
            <circle cx="12" cy="12" r="10" fill="var(--gold-dark)"/>
            <ellipse cx="12" cy="12" rx="4" ry="10" fill="none" stroke="#fff" stroke-width="1.4"/>
            <path d="M2 12h20" stroke="#fff" stroke-width="1.4"/>
          </svg>
          www.plumvora.example
        </li>
      </ul>
    </section>

    <div class="divider"></div>

    <address class="locations" style="font-style: normal;">
      United Kingdom<br>
      Australia, New Zealand
    </address>
  </article>
</body>
</html>
```